Locksmith Business Cards

My father-in-law is in need of new business cards for his locksmith business and I need to impress him. Kindly help me out!

You can see the previous business card attached. It is a family run business in North Wales.

No individual names on the cards.

Key Things to Feature:
- The words "Prompt", "Local", "Reliable" (as you can see under the logo on the website)
- 24h Emergency Service
- Covering All of North Wales, the Wirral and Chester
- The color blue
- A key or a lock would be interesting (similar to the ones that come up when you google locksmith business card)

Optional (only if design includes bullet points, like the example below):
https://imgvaultcdn.net/samples/208314/55172/55172_3904821_208314_image.jpg
- Residential / Commercial / Automotive
- Alarms & Cameras
- Key Cutting & Safes

https://www.brynhafod-locksmiths.co.uk/

Industry/Entity Type

Locksmith

Contact Information for Business Card

01632 960 418
07700 900 362
brynhafodlocksmiths@mailvane.com
Brynhafod Locksmiths, The Willow Barn, 7 Tannery Rd., Llandudno LL99 4QX
www.brynhafod-locksmiths.co.uk

Requirements
Must have
• - The words "Prompt", "Local", "Reliable" (as you can see under the logo on the website)
• - 24h Emergency Service
• - Covering All of North Wales, the Wirral and Chester
Nice to have
• - A key or a lock would be interesting (similar to the ones that come up when you google locksmith business card)

```html
<!DOCTYPE html>
<html lang="en">
<head>
<meta charset="utf-8">
<title>Brynhafod Locksmiths – Business Cards</title>
<link href="https://fonts.googleapis.com/css2?family=Oswald:wght@500&family=Saira+Semi+Condensed:wght@500&family=Montserrat:wght@600&display=swap" rel="stylesheet">
<style>
  :root {
    --page: #e6e7ea;
    --card: #f3f3f4;
    --navy: #252f78;
    --royal: #3b4a9e;
    --band: #4c5daa;
    --dot: #5cc3ee;
    --white: #ffffff;
  }
  * { margin: 0; padding: 0; box-sizing: border-box; }
  html, body { width: 1200px; height: 1050px; overflow: hidden; background: var(--page); }
  .sheet { position: relative; width: 1200px; height: 1050px; }

  .card {
    position: absolute; left: 200px; width: 800px; height: 457px;
    background: var(--card); border-radius: 28px; overflow: hidden;
    box-shadow: 0 6px 22px rgba(0,0,0,.18);
  }
  .card--front { top: 50px; }
  .card--back { top: 545px; }

  .brand { position: absolute; display: flex; align-items: center; gap: 18px; }
  .brand__dot { width: 74px; height: 74px; border-radius: 50%; background: var(--navy); flex: none; }
  .brand__name {
    font-family: "Oswald", sans-serif; font-weight: 500; color: var(--navy);
    font-size: 46px; line-height: 0.95; text-transform: uppercase; letter-spacing: .5px;
  }
  .tagline {
    position: absolute; font-family: "Montserrat", sans-serif; font-weight: 600;
    font-size: 17px; letter-spacing: 2px; color: var(--royal); text-transform: uppercase;
    white-space: nowrap;
  }
  .tagline span { margin: 0 10px; }

  .services {
    list-style: none; font-family: "Saira Semi Condensed", sans-serif; font-weight: 500;
    color: var(--white); white-space: nowrap;
  }
  .services li { position: relative; }

  /* front */
  .front__arc {
    position: absolute; left: 420px; top: -300px; width: 640px; height: 700px;
    border-radius: 50%; background: var(--royal);
  }
  .front__services { position: absolute; right: 78px; top: 80px; text-align: right; font-size: 21px; line-height: 1.38; }
  .front__services li::after {
    content: ""; position: absolute; right: -26px; top: 50%; width: 8px; height: 8px;
    margin-top: -4px; border-radius: 50%; background: var(--dot);
  }
  .card--front .brand { left: 80px; top: 270px; }
  .card--front .tagline { left: 172px; top: 378px; }

  /* back */
  .card--back .brand { left: 56px; top: 98px; }
  .back__panel {
    position: absolute; left: 420px; top: 118px; right: 0; height: 210px;
    background: var(--navy); border-radius: 26px 0 0 26px;
  }
  .back__services { position: absolute; left: 458px; top: 136px; font-size: 17px; line-height: 1.5; }
  .back__services li::before {
    content: ""; position: absolute; left: -20px; top: 50%; width: 7px; height: 7px;
    margin-top: -3.5px; border-radius: 50%; background: var(--dot);
  }
  .back__band {
    position: absolute; left: 0; top: 238px; width: 420px; height: 160px; background: var(--band);
  }
  .contact {
    position: absolute; left: 56px; top: 250px; list-style: none;
    font-family: "Saira Semi Condensed", sans-serif; font-weight: 500;
    color: var(--white); font-size: 16px; line-height: 1.3; white-space: nowrap;
  }
  .contact li { display: flex; align-items: flex-start; gap: 12px; }
  .contact svg { width: 14px; height: 14px; margin-top: 3px; flex: none; fill: var(--white); }
  .card--back .tagline { left: 56px; top: 412px; color: var(--navy); }
</style>
</head>
<body>
<main class="sheet">

  <section class="card card--front" aria-label="Card front">
    <div class="front__arc"></div>
    <ul class="services front__services">
      <li>24h Emergency Service</li>
      <li>Covering All of North Wales,</li>
      <li>the Wirral and Chester</li>
      <li>Residential / Commercial</li>
      <li>Automotive</li>
      <li>Alarms &amp; Cameras</li>
      <li>Key Cutting &amp; Safes</li>
    </ul>
    <div class="brand">
      <span class="brand__dot"></span>
      <p class="brand__name">Brynhafod<br>Locksmiths</p>
    </div>
    <p class="tagline">Prompt<span>|</span>Local<span>|</span>Reliable</p>
  </section>

  <section class="card card--back" aria-label="Card back">
    <div class="brand">
      <span class="brand__dot"></span>
      <p class="brand__name">Brynhafod<br>Locksmiths</p>
    </div>
    <div class="back__panel"></div>
    <ul class="services back__services">
      <li>24h Emergency Service</li>
      <li>Covering All of North Wales,</li>
      <li>the Wirral and Chester</li>
      <li>Residential / Commercial / Automotive</li>
      <li>Alarms &amp; Cameras</li>
      <li>Key Cutting &amp; Safes</li>
    </ul>
    <div class="back__band"></div>
    <ul class="contact">
      <li><svg viewBox="0 0 16 16"><path d="M3 1l3 0 1 4-2 1.5a9 9 0 004.5 4.5L11 9l4 1v3a2 2 0 01-2 2A12 12 0 011 3a2 2 0 012-2z"/></svg>01632 960 418</li>
      <li><svg viewBox="0 0 16 16"><path d="M3 1l3 0 1 4-2 1.5a9 9 0 004.5 4.5L11 9l4 1v3a2 2 0 01-2 2A12 12 0 011 3a2 2 0 012-2z"/></svg>07700 900 362</li>
      <li><svg viewBox="0 0 16 16"><path d="M1 3h14v10H1z M1 3l7 6 7-6" fill="none" stroke="#fff" stroke-width="1.6"/></svg>brynhafodlocksmiths@mailvane.com</li>
      <li><svg viewBox="0 0 16 16"><circle cx="8" cy="8" r="6.5" fill="none" stroke="#fff" stroke-width="1.5"/><path d="M1.5 8h13M8 1.5c-3 3-3 10 0 13M8 1.5c3 3 3 10 0 13" fill="none" stroke="#fff" stroke-width="1.2"/></svg>www.brynhafod-locksmiths.co.uk</li>
      <li><svg viewBox="0 0 16 16"><path d="M8 0a5.5 5.5 0 015.5 5.5C13.5 10 8 16 8 16S2.5 10 2.5 5.5A5.5 5.5 0 018 0zm0 3.5a2 2 0 100 4 2 2 0 000-4z"/></svg>The Willow Barn, 7 Tannery Rd.,<br>Llandudno LL99 4QX</li>
    </ul>
    <p class="tagline">Prompt<span>|</span>Local<span>|</span>Reliable</p>
  </section>

</main>
</body>
</html>
```